Meadowlark Property Review is a leading provider of residential appraisal and home inspection products in S

I need a business card/logo designed that obviously describes my business. We are a residential appraisal and home inspection company in Springfield, MO. We offer residential appraisals, home inspection, pest inspection and radon gas measurement. We have been in business for 18 years and hold state certified residential appraisal licenses and OBREX certified home inspection licenses. I have a logo that I really like and will attach, but would be open to new suggestions. I like more modern designs than traditional and would like a two sided card with our services, licenses and qualifications on the back.

```html
<!DOCTYPE html>
<html lang="en">
<head>
<meta charset="utf-8">
<title>Meadowlark Property Review – Business Card</title>
<link rel="stylesheet" href="https://fonts.googleapis.com/css2?family=Source+Sans+3:ital,wght@0,400;0,600;0,700;1,400&display=swap">
<style>
  :root {
    --backdrop: #e9e4dd;
    --frost: #dcdad6;
    --frost-edge: #c9c6c1;
    --panel-brown: #7b5a45;
    --panel-brown-dark: #5e4333;
    --accent-orange: #e0702a;
    --divider-orange: #c8601f;
    --text-light: #f4ece4;
    --text-soft: #e6d6c8;
    --brand-brown: #5a3b27;
  }
  * { box-sizing: border-box; margin: 0; padding: 0; }
  html, body {
    width: 1200px; height: 969px; overflow: hidden;
    background: var(--backdrop);
    font-family: "Source Sans 3", "Helvetica Neue", Arial, sans-serif;
  }
  .canvas { position: relative; width: 1200px; height: 969px; }
  .card {
    position: absolute; left: 150px; top: 228px;
    width: 900px; height: 512px;
    border-radius: 22px; overflow: hidden;
    background: linear-gradient(160deg, #e6e4e1 0%, var(--frost) 55%, #d2cfca 100%);
    border: 1px solid var(--frost-edge);
    box-shadow: 0 18px 40px rgba(60, 45, 35, 0.22);
  }
  .contact-panel {
    position: absolute; left: 0; top: 0; bottom: 0; width: 428px;
    background: linear-gradient(170deg, #866452 0%, var(--panel-brown) 45%, var(--panel-brown-dark) 100%);
    padding: 38px 0 0 46px;
    color: var(--text-light);
  }
  .divider { position: absolute; left: 418px; top: 0; width: 30px; height: 512px; }
  .person-name { font-size: 30px; font-weight: 600; color: var(--accent-orange); line-height: 1.1; }
  .person-title { font-size: 23px; color: var(--text-light); margin-top: 6px; }
  .address { font-size: 20px; line-height: 1.32; margin-top: 24px; color: var(--text-light); }
  .contact-list { list-style: none; margin-top: 22px; }
  .contact-list li {
    display: flex; align-items: center; gap: 14px;
    font-size: 20px; line-height: 34px; color: var(--text-light);
  }
  .contact-list svg { width: 20px; height: 20px; flex: none; }
  .services { list-style: none; margin-top: 18px; }
  .services li {
    position: relative; padding-left: 26px;
    font-size: 21px; font-style: italic; line-height: 29px; color: var(--text-soft);
  }
  .services li::before {
    content: ""; position: absolute; left: 2px; top: 12px;
    width: 7px; height: 7px; border-radius: 50%; background: var(--accent-orange);
  }
  .services li.continued::before { display: none; }
  .brand {
    position: absolute; left: 448px; right: 0; top: 0; bottom: 0;
    display: flex; align-items: center; justify-content: center; gap: 14px;
  }
  .brand-mark { width: 22px; height: 22px; background: var(--accent-orange); flex: none; }
  .brand-name { font-size: 30px; font-weight: 700; color: var(--brand-brown); letter-spacing: 0.3px; }
</style>
</head>
<body>
<div class="canvas">
  <section class="card" aria-label="Business card front">
    <div class="contact-panel">
      <h1 class="person-name">Dana Whitfield</h1>
      <p class="person-title">CEO/Founder</p>
      <p class="address">2140 Birchwood Court<br>Springfield, Missouri 65804</p>
      <ul class="contact-list">
        <li>
          <svg viewBox="0 0 20 20" aria-hidden="true"><path fill="var(--accent-orange)" d="M5 2l3 4-2 2c1 2.5 3.5 5 6 6l2-2 4 3-2 3C9 18 2 11 2 4z"/></svg>
          417 555 0182
        </li>
        <li>
          <svg viewBox="0 0 20 20" aria-hidden="true"><path fill="var(--accent-orange)" d="M5 2h10v5H5zM2 8h16v8h-3v-3H5v3H2zM6 14h8v4H6z"/></svg>
          417 555 0147
        </li>
        <li>
          <svg viewBox="0 0 20 20" aria-hidden="true"><rect x="2" y="4" width="16" height="12" rx="1" fill="var(--accent-orange)"/><path d="M2.5 5l7.5 6 7.5-6" fill="none" stroke="#7b5a45" stroke-width="1.5"/></svg>
          hello@meadowlarkreview.com
        </li>
        <li>
          <svg viewBox="0 0 20 20" aria-hidden="true"><circle cx="10" cy="10" r="8" fill="var(--accent-orange)"/><path d="M2 10h16M10 2c-3 3-3 13 0 16M10 2c3 3 3 13 0 16" fill="none" stroke="#7b5a45" stroke-width="1.2"/></svg>
          www.meadowlarkreview.com
        </li>
      </ul>
      <ul class="services">
        <li>Residential appraisals</li>
        <li>Home inspection</li>
        <li>Pest inspection and</li>
        <li>radon gas measurement.</li>
      </ul>
    </div>
    <svg class="divider" viewBox="0 0 30 512" aria-hidden="true">
      <path d="M10 0V86L22 100L10 114V512" fill="none" stroke="var(--divider-orange)" stroke-width="4"/>
    </svg>
    <div class="brand">
      <span class="brand-mark"></span>
      <span class="brand-name">Meadowlark Property Review</span>
    </div>
  </section>
</div>
</body>
</html>
```